White Paper and One-Page Advertisement for TELVORISH-QM

I need both documents to be better formatted and designed so they look professional, not something someone with mediocre word skills put together. They will go out to 1000s of industry professionals, and they need to look sharp. I need them to have my company's color palate logo, and branding on it similar to how it is now, but better. Please do not change any of the written content, but it can be arranged in any other format you think is better. Smart art and things i've already used can be omitted in favor of better designs. The developer is free to use their creativity. White paper should not be longer than the three pages unless necessary.

Target Market(s)

Life Sciences supply chain professionals

Colors
33b8a4
0592cd
9bcb3c
fbee3e
3277b5

Requirements
Must have
• Must be professional looking and not look like something done in word. Please use the color palate as seen on the documents.
Should not have
• Any changes to the written content.

```html
<!DOCTYPE html>
<html lang="en">
<head>
<meta charset="utf-8">
<title>Changing Pharma's Paradigm of Waste – White Paper</title>
<link href="https://fonts.googleapis.com/css2?family=Montserrat:wght@500;600;700&family=Open+Sans:wght@400;600&display=swap" rel="stylesheet">
<style>
  :root{
    --green:#9bcb3c;
    --green-deep:#5aad2e;
    --green-dark:#3f9a2a;
    --navy:#3a4a5c;
    --ink:#55595e;
    --paper:#f7f7f5;
    --stage:#e4e5e6;
  }
  *{box-sizing:border-box;margin:0;padding:0}
  html,body{width:858px;height:1200px;overflow:hidden;background:var(--stage)}
  body{font-family:"Open Sans",Arial,sans-serif;color:var(--ink)}
  .canvas{position:relative;width:858px;height:1200px}
  .spread{position:absolute;left:20px;width:818px;height:578px;display:flex;box-shadow:0 6px 18px rgba(0,0,0,.18)}
  .spread--outside{top:12px}
  .spread--inside{top:610px}
  .page{position:relative;width:409px;height:578px;background:var(--paper);overflow:hidden}
  .page + .page{border-left:1px solid #dcdcdc}
  .band{position:absolute;left:0;width:409px}
  .band--top{top:0;height:40px}
  .band--bottom{bottom:0;height:70px}
  .content{position:absolute;left:30px;right:30px}
  h2.section{font-family:"Montserrat",Arial,sans-serif;font-weight:600;color:var(--green-deep);letter-spacing:.5px}
  h3.sub{font-family:"Montserrat",Arial,sans-serif;font-size:7px;font-weight:600;color:var(--green-deep);margin:5px 0 2px}
  p.body{font-size:5.2px;line-height:1.5;margin-bottom:3px}
  ul.list{list-style:none;font-size:5.2px;line-height:1.55}
  ul.list li::before{content:"";display:inline-block;width:3px;height:3px;background:var(--navy);border-radius:50%;margin-right:4px;vertical-align:middle}
  .photo-hex{position:absolute}
  /* cover */
  .cover-title{font-family:"Montserrat",Arial,sans-serif;font-weight:700;color:var(--green);font-size:25px;line-height:1.05;text-align:center;letter-spacing:1px}
  .cover-sub{font-family:"Montserrat",Arial,sans-serif;font-weight:600;color:var(--navy);font-size:11px;line-height:1.25;text-align:center;margin-top:8px}
  .cover-author{font-family:"Montserrat",Arial,sans-serif;font-weight:700;color:var(--navy);font-size:19px;text-align:center;margin-top:8px;letter-spacing:1px}
  .cover-date{font-family:"Montserrat",Arial,sans-serif;font-weight:600;color:var(--green);font-size:11px;text-align:center;letter-spacing:1px}
  .brand{display:flex;align-items:center;justify-content:center;gap:5px;margin-top:14px}
  .brand-dot{width:9px;height:9px;border-radius:50%;background:var(--green-deep)}
  .brand-name{font-family:"Open Sans",Arial,sans-serif;font-weight:600;font-size:10px;color:var(--green-deep);letter-spacing:.5px}
  .cover-section{font-size:16px;margin-top:12px;margin-bottom:3px}
  /* contact */
  .contact{position:absolute;right:28px;bottom:12px;text-align:right;color:var(--navy)}
  .contact h2{font-family:"Montserrat",Arial,sans-serif;font-weight:700;color:var(--green-deep);font-size:16px;letter-spacing:1px}
  .contact p{font-size:6.5px;line-height:1.45}
  .overview-title{font-size:19px;font-weight:700;margin-bottom:6px}
  .footer-note{position:absolute;right:24px;bottom:22px;text-align:right;font-size:5px;color:#fff;line-height:1.5}
</style>
</head>
<body>
<main class="canvas">

  <!-- Outside spread: back page and front cover -->
  <section class="spread spread--outside">
    <article class="page page--back">
      <svg class="band band--top" viewBox="0 0 409 40" preserveAspectRatio="none" aria-hidden="true">
        <polygon points="200,0 409,0 409,8 240,8" fill="var(--green-deep)"/>
      </svg>
      <div class="content" style="top:22px">
        <h3 class="sub">Current State</h3>
        <p class="body">Pharma and other FDA regulated industries spend considerable energy on reducing waste. A portion of techniques are employed to mitigate losses, but surplus materials still leave the building as write-downs and disposal costs every year.</p>
        <h3 class="sub">Market Influences</h3>
        <p class="body">Demand volatility, shorter product cycles and stricter regulations push firms to hold larger safety stock. When forecasts shift, this stock turns into idle inventory that is rarely recovered or reused.</p>
        <h3 class="sub">Unexplored Solutions</h3>
        <p class="body">Few companies have a trusted channel to move surplus materials to qualified buyers. Current practice favours disposal because it is simple, even when the material remains fully usable and compliant.</p>
        <h3 class="sub">Root Cause &amp; Barriers</h3>
        <p class="body">Quality concerns, limited traceability and a lack of shared standards keep organisations from trading materials. Buyers need verified documentation; sellers need a compliant and confidential process.</p>
        <h3 class="sub">Future State</h3>
        <p class="body">A life sciences marketplace and consortium where manufacturers, researchers and suppliers exchange materials with full chain of custody, shared audits and clear pricing for every transaction.</p>
        <h3 class="sub">Benefits</h3>
        <ul class="list">
          <li>Lower write-downs and disposal spend across the network</li>
          <li>Faster access to scarce materials for research programs</li>
          <li>Verified supply with documentation held in one place</li>
          <li>Measurable reduction in environmental footprint</li>
        </ul>
        <h3 class="sub">How to Implement</h3>
        <p class="body">Join the consortium, list surplus materials, align on quality agreements and use shared supplier audits. Each member follows the same standards so every exchange remains compliant with FDA guidance.</p>
        <h3 class="sub">Data Integrity</h3>
        <p class="body">Data follows ALCOA principles; all records are attributable, legible and traceable to protect buyers and sellers alike.</p>
      </div>
      <svg class="photo-hex" style="left:20px;bottom:62px" width="74" height="66" viewBox="0 0 74 66" role="img" aria-label="Photo of a smiling child in a clinical setting">
        <defs><linearGradient id="hexA" x1="0" y1="0" x2="1" y2="1"><stop offset="0" stop-color="#c9b8a3"/><stop offset="1" stop-color="#6b5a4a"/></linearGradient></defs>
        <polygon points="18,1 56,1 73,33 56,65 18,65 1,33" fill="url(#hexA)" stroke="var(--green-deep)" stroke-width="2"/>
      </svg>
      <svg class="band band--bottom" viewBox="0 0 409 70" preserveAspectRatio="none" aria-hidden="true">
        <polygon points="0,10 200,50 409,40 409,70 0,70" fill="var(--green)"/>
        <polygon points="0,22 230,58 409,52 409,70 0,70" fill="var(--green-deep)"/>
      </svg>
      <div class="contact" style="bottom:78px">
        <h2>CONTACT</h2>
        <p>Visit : www.telvorishqm.com<br>Email : info@telvorishqm.com<br>Read our : white paper</p>
      </div>
    </article>

    <article class="page page--cover">
      <svg class="band band--top" viewBox="0 0 409 40" preserveAspectRatio="none" aria-hidden="true">
        <polygon points="0,0 409,0 409,26 0,6" fill="var(--green)"/>
        <polygon points="0,0 409,0 409,12 0,2" fill="var(--green-deep)"/>
      </svg>
      <div class="content" style="top:52px">
        <h1 class="cover-title">CHANGING PHARMA'S<br>PARADIGM OF WASTE</h1>
        <p class="cover-sub">How Pharma's Demand Volatility Could Be Costing You Millions in Material Write-downs &amp; Procurement</p>
        <p class="cover-author">DANA WHITCOMBE</p>
        <p class="cover-date">AUGUST 2018</p>
        <div class="brand"><span class="brand-dot"></span><span class="brand-name">TELVORISH-QM</span></div>

        <h2 class="section cover-section">OUR PLATFORM</h2>
        <ul class="list">
          <li>A multi-vendor marketplace for the life science community to transact pre-market and after-market materials and equipment</li>
          <li>Researchers, manufacturers and original suppliers can create an account to buy, sell, or donate materials</li>
          <li>Part 11 compliant signatures and digital records for transparent transactions</li>
          <li>Shared supplier audits and quality agreements built into every listing</li>
        </ul>
        <h2 class="section cover-section">BENEFITS</h2>
        <ul class="list">
          <li>Reduce write-offs by selling excess and obsolete materials, equipment, spare parts, etc.</li>
          <li>Buy quality materials at a reduced price</li>
          <li>Donate materials to researchers</li>
          <li>Collaborate and connect to reduce supply chain risk</li>
        </ul>
        <h2 class="section cover-section">OUR PROMISE</h2>
        <ul class="list">
          <li>A collaborative life sciences marketplace with a transparent, compliant supply chain</li>
        </ul>
      </div>
      <svg class="band band--bottom" viewBox="0 0 409 70" preserveAspectRatio="none" aria-hidden="true">
        <polygon points="0,8 409,48 409,70 0,70" fill="var(--green)"/>
        <polygon points="0,30 409,58 409,70 0,70" fill="var(--green-deep)"/>
      </svg>
    </article>
  </section>

  <!-- Inside spread -->
  <section class="spread spread--inside">
    <article class="page page--overview">
      <svg class="band band--top" viewBox="0 0 409 40" preserveAspectRatio="none" aria-hidden="true">
        <polygon points="0,0 409,0 409,6 0,16" fill="var(--green)"/>
        <polygon points="0,0 409,0 409,2 0,7" fill="var(--green-deep)"/>
      </svg>
      <div class="content" style="top:30px">
        <h2 class="section overview-title">OVERVIEW</h2>
        <p class="body">Demand volatility is a challenge for every supply chain. In times of low demand, materials purchased for forecasted production become idle and are eventually written off. In times of high demand, the same materials become scarce and costly to procure quickly. Both situations create waste and drive up the cost of getting therapies to patients.</p>
        <p class="body">Industry surveys estimate that a significant share of purchased materials is never consumed. These losses are rarely tracked as one figure, so the true impact on margins stays hidden inside inventory adjustments, destruction fees and expedited orders.</p>
        <h3 class="sub">What Do These Numbers Mean?</h3>
        <p class="body"><strong>$77B is an alarmingly high</strong> estimate, and it does not include capitalized consumables, equipment disposal and similar losses.</p>
        <p class="body"><strong>$2.7B is likely much lower than the real figure</strong> due to capitalized inventories for launches.</p>
        <p class="body"><strong>$2.0 to one ton of industrial waste is not progressive.</strong></p>
        <p class="body">Industries have attempted to mitigate the problem with lean practices, forecasting models and better planning. These tools help, yet they cannot remove the uncertainty that comes with clinical trials, regulatory approvals and shifting market demand.</p>
        <p class="body">A life sciences marketplace and consortium gives companies a compliant way to move surplus materials to the people who need them. Sellers recover value, buyers save on procurement and less material ends in landfill or incineration.</p>
        <p class="body">Let us explore current and future state of this industry and understand why such a marketplace has not yet become common practice.</p>
        <h3 class="sub">Undesirable Solutions</h3>
        <p class="body">Unfortunately, third party disposal frequently results in landfill, incineration or inactivation, while usable materials are destroyed at a cost.</p>
        <h3 class="sub">Overall</h3>
        <p class="body">Industries spend much capital and resources to reduce write-downs in an environment where volatility cannot be controlled.</p>
        <h3 class="sub">Refined Problem</h3>
        <p class="body">There is no clear market leader that helps organisations trade surplus materials with confidence. A trusted marketplace must offer quality data, traceability and secure transactions so that every participant benefits from the exchange.</p>
      </div>
      <svg class="band band--bottom" viewBox="0 0 409 70" preserveAspectRatio="none" aria-hidden="true">
        <polygon points="0,40 409,30 409,70 0,70" fill="var(--green)"/>
        <polygon points="0,54 409,48 409,70 0,70" fill="var(--green-deep)"/>
      </svg>
    </article>

    <article class="page page--environment">
      <svg class="band band--top" viewBox="0 0 409 40" preserveAspectRatio="none" aria-hidden="true">
        <polygon points="0,16 409,0 409,14 0,28" fill="var(--green)"/>
        <polygon points="0,10 409,0 409,5 0,16" fill="var(--green-deep)"/>
      </svg>
      <div class="content" style="top:34px">
        <h3 class="sub">Contemporary Operating Environment</h3>
        <p class="body">Constant pressure from global competition, increasing customer and governmental demand for price, more regulatory scrutiny and a marketplace that is still fragmented leave organisations looking for new ways to protect margins.</p>
        <p class="body">Regulators are cooperative and open to solutions. Collaborative supply chains are emerging and pharma continues to struggle with the bullwhip effect.</p>
        <h3 class="sub">How to Find Out More</h3>
        <p class="body">The exciting new marketplace called TELVORISH-QM is scheduled for initial launch in November 2018. We are an emerging small business with the ultimate goal to educate, inspire and align pharma around a new paradigm of waste reduction and sourcing strategies.</p>
        <h3 class="sub">Sources</h3>
        <ul class="list">
          <li>Top 100 pharma companies, annual industry report</li>
          <li>Global life sciences waste survey, 2016</li>
          <li>Supply chain benchmarking study, 2017</li>
          <li>Environmental impact review, 2015</li>
        </ul>
        <h3 class="sub">Baseline Problem</h3>
        <ul class="list">
          <li>Disposal of high quality materials, equipment, spare parts</li>
          <li>Single and limited sources of supply</li>
          <li>Inability to collaborate with like-minded firms</li>
          <li>High COGS due to material write-downs</li>
          <li>High inventory carrying costs</li>
          <li>Greater business continuity risk</li>
          <li>Larger environmental footprint</li>
        </ul>
        <h3 class="sub">Who?</h3>
        <p class="body">FDA regulated industries: procurement, quality, production, R&amp;D, planning and finance.</p>
        <h3 class="sub">Financials</h3>
        <ul class="list">
          <li>Vendors / sellers: higher write-downs and disposal fees</li>
          <li>Buyers: lost sales and stock-outs</li>
          <li>Inflated market value of materials</li>
          <li>Greater contribution to global warming through landfill and incineration</li>
        </ul>
      </div>
      <svg class="photo-hex" style="left:150px;bottom:54px" width="58" height="52" viewBox="0 0 58 52" role="img" aria-label="Photo of a young woman">
        <defs><linearGradient id="hexB" x1="0" y1="0" x2="1" y2="1"><stop offset="0" stop-color="#8a6a55"/><stop offset="1" stop-color="#2e2420"/></linearGradient></defs>
        <polygon points="14,1 44,1 57,26 44,51 14,51 1,26" fill="url(#hexB)" stroke="var(--green-deep)" stroke-width="2"/>
      </svg>
      <svg class="photo-hex" style="left:202px;bottom:70px" width="74" height="66" viewBox="0 0 74 66" role="img" aria-label="Photo of a smiling elderly woman">
        <defs><linearGradient id="hexC" x1="0" y1="0" x2="1" y2="1"><stop offset="0" stop-color="#dfe3e6"/><stop offset="1" stop-color="#7d8a96"/></linearGradient></defs>
        <polygon points="18,1 56,1 73,33 56,65 18,65 1,33" fill="url(#hexC)" stroke="var(--green-deep)" stroke-width="2"/>
      </svg>
      <svg class="band band--bottom" viewBox="0 0 409 70" preserveAspectRatio="none" aria-hidden="true">
        <polygon points="0,36 409,20 409,70 0,70" fill="var(--green)"/>
        <polygon points="0,50 409,42 409,70 0,70" fill="var(--green-deep)"/>
      </svg>
      <p class="footer-note" style="bottom:78px;color:var(--green-dark)">Email Dana Whitcombe<br>Visit www.telvorishqm.com</p>
    </article>
  </section>

</main>
</body>
</html>
```